Website development company website

ABOUT COMPANY
Hi everyone! We're a Melbourne, Australia website development company in a need of a website design that will make online store merchants want to engage our services.
We specialise exclusively in Torvista e-commerce platform (https://torvista-platform.example/). What distinguishes our business from competition is that rather than designing and building brand new websites, we offer development, support and maintenance services to established websites. Maintenance and Support are the keywords representing our business.
Our potential clients are people with broken, slow and underperforming Torvista installations who need assistance getting their websites up and making sales. Our website must pass the message that we can help, and provide quick means of making contact.
DESIGN
Overall, we're looking for a slick, clean, airy, conservative design. No need to do anything crazy, try to stick to what's "standard" in website design these days and make it easy on all of us. The website is unlikely to be updated too often so it needs to look attractive and fresh first time over and after a year, too.
Attached is our new logo, which you'll be able to take the basic idea from, the colors and fonts. Though, don't use the fonts from the logo in the website, stick to the standard widely supported fonts. Additional use of Google fonts is fine.
Don't overdo it with colors, stick to conservative basic color set and only use the colors from the log for accents like headings etc. Please, don't be tempted to use the blue and orange as background of whole blocks, other than perhaps footer. Thanks.
For the images used, I'd like to stay away from a design studio/digital agency feel and lean more towards professional support and maintenance services. I'm thinking images of content merchants doing their job. Something along the lines of "We'll be taking care of the website so that you only need to care about the business".
Some ideas I like:
http://www.plumframe-pics.example/detail/photo/portrait-of-confident-male-design-professional-royalty-free-image/572048163
http://www.plumframe-pics.example/detail/photo/designer-taking-picture-of-hat-high-res-stock-photography/839207514
http://www.plumframe-pics.example/detail/photo/woman-packaging-pottery-royalty-free-image/216684093
Images of colorful shopping bags and shopping carts are over the top and not serious enough. Instead of images matching Online Shopping, I'd try going more for Stability, Reliability, Performance.
Our existing website is http://www.bravuln.example. Please, don't take design ideas from it, but it will give you a picture of the structure of our new website and content that's going to be used initially.
If you could include a basic icon set to use throughout the website, that would be great. If the icons could match our logo (attached), it would be a big plus.
ALL PAGES
Every page must contain clearly visible phone number (1300 648 907) and a Contact Us Now button, which opens an AJAX driven popup form with Name, Email, Phone and Message to be sent through.
To start with, main menu items will be Torvista, Portfolio, Contact.
At the bottom of each page, please, include a newsletter subscription form with text Subscribe to Torvista Support and Security Updates.
For the footer, I'd like to see a logo strip with the following logos in grayscale (no need to link anywhere): Torvista, QRX, DataVane, NCB. You'll find the logos on Google Images.
Standard footer columns follow. Here, I'd like to see logos in color: Torvista Certified Developer, Torvista Ceritified Solution Provider. Again, the logos are on Google Images.
No social media logos/links necessary anywhere on the website.
...and then the copyright line.
FRONT PAGE
Large slider with images that would appeal to our target audience. Keywords here would be Torvista System Audit, Torvista Performance Optimisation, Torvista Website Emergency Recovery, Torvista Development Infrastructure Hosting. We'll have a static page created for each of these to link to.
In a corner of the slider, or on the edge, can I have an overlay with logos in color (same as footer): Torvista Certified Developer, Torvista Ceritified Solution Provider.
Underneath, a number of blocks, each with an image and teaser that we'll use to link to various pages throughout the website.
PORTFOLIO PAGE
I'm thinking a single long page with a block per client, which will contain project name, description from us and a testimonial from client. Also, each block will contain a single large screenshot. No gallery or slideshow is necessary here, just one image per project.
I'll leave the layout up to you, but try to put yourself in the shoes of a potential client reviewing our past work by simply scrolling down this one page.
CONTACT US PAGE
Separate page with the same form as above, phone number (1300 648 907), email address (support@kavreo.example), address (Suite 42, Level 3|8 Wattlebrook Lane|Fernvale Heights VIC 3999), and a grayscale Google Map.
CODING UP
Coding up into static HTML/CSS/JS is equally important as the design itself. We're a website development company, we'll be integrating the theme. We will spot any issues and we will point them out.
Coded up design must be fully responsive. Enough said.
To be able to create any content in future, we'd like one extra page coded up with samples of all themed elements, lists, forms, buttons, 2, 3, 4-column layout, alerts, icons, etc. This page does not need to be designed, only coded up.
The design will be integrated into Drupal using Twig. If possible at all, try to keep it in mind when designing and coding up, and make the integration into a Drupal theme easier for us.
GOOD LUCK!
That's it. Let me know if anything needs clarifying. So far I've had a great experience with ArtFlockly. I don't doubt some great designs will emerge. Clever ideas are highly appreciated, but also make it clear you've read and followed the points in this brief. Cheers, Tom

```html
<!DOCTYPE html>
<html lang="en">
<head>
<meta charset="utf-8">
<title>Kavreo eCommerce – Torvista Support &amp; Maintenance</title>
<link href="https://fonts.googleapis.com/css2?family=Roboto:ital,wght@0,300;0,400;0,500;0,700;1,400&family=Roboto+Condensed:wght@400;700&display=swap" rel="stylesheet">
<style>
:root{
  --orange:#ea7a1e;
  --orange-dark:#d66a12;
  --navy:#123f73;
  --navy-deep:#0e3563;
  --ink:#333;
  --muted:#666;
  --light:#f3f3f3;
  --white:#fff;
}
*{box-sizing:border-box;margin:0;padding:0}
html,body{width:1200px;height:3303px;overflow:hidden}
body{font-family:"Roboto",Arial,sans-serif;color:var(--ink);background:var(--white);position:relative}
.block{position:absolute;left:0;width:1200px}
.abs{position:absolute}
.btn{display:inline-block;font-family:"Roboto",Arial,sans-serif;font-size:14px;font-weight:500;text-transform:uppercase;text-decoration:none;letter-spacing:.3px}

/* top bar */
.topbar{top:0;height:33px;background:var(--orange);color:var(--white);font-size:12px}
.topbar-links{position:absolute;right:95px;top:9px;display:flex;gap:34px}
.topbar-links span{display:flex;align-items:center;gap:7px}

/* header */
.header{top:33px;height:88px;background:var(--white);box-shadow:0 1px 3px rgba(0,0,0,.08);z-index:2}
.brand{position:absolute;left:98px;top:18px;display:flex;align-items:center;gap:10px}
.brand-mark{width:34px;height:34px;background:var(--navy);border-radius:4px}
.brand-name{font-family:"Roboto",Arial,sans-serif;font-weight:700;font-size:34px;color:var(--navy);line-height:1}
.nav{position:absolute;right:96px;top:38px;display:flex;gap:42px;font-size:13px;text-transform:uppercase;color:var(--ink)}
.nav .active{color:var(--orange)}

/* hero */
.hero{top:121px;height:557px;background:linear-gradient(100deg,#3f3a36 0%,#6b5a4d 35%,#a58670 60%,#d9c3ae 100%)}
.hero-text{left:97px;top:212px;color:var(--white);font-family:"Roboto Condensed",Arial,sans-serif;text-transform:uppercase}
.hero-text h1{font-size:38px;font-weight:400;line-height:1.05}
.hero-text h2{font-size:30px;font-weight:400;line-height:1.2}
.hero-btn{left:97px;top:308px;background:var(--orange);color:var(--white);padding:12px 22px;font-size:13px}
.hero-arrow{top:270px;color:rgba(255,255,255,.6);font-size:40px}
.badge{top:418px;width:68px;height:116px;border-radius:6px}

/* welcome */
.welcome{top:678px;height:420px;background:linear-gradient(115deg,#f1f1f1 0%,#f7f7f7 55%,#fff 55%)}
.welcome-title{left:112px;top:70px;font-family:"Roboto Condensed",Arial,sans-serif;line-height:1.1}
.welcome-title .l1{font-size:44px;color:#333}
.welcome-title .l2{font-size:42px;color:var(--navy)}
.welcome-copy{left:112px;top:186px;width:530px;font-size:11.5px;line-height:1.85;color:var(--muted)}
.welcome-copy p+p{margin-top:8px}
.welcome-btn{left:112px;top:313px;background:var(--navy);color:var(--white);padding:10px 24px;font-size:12px}
.welcome-art{left:820px;top:55px;width:230px;height:310px;border-radius:6px;background:linear-gradient(160deg,var(--orange),var(--navy))}

/* services */
.services{top:1098px;height:514px;background:linear-gradient(120deg,#2f5c8c,#214b7b 55%,#2f5f86)}
.section-title{width:100%;text-align:center;font-family:"Roboto Condensed",Arial,sans-serif;font-size:31px;font-weight:400}
.services .section-title{top:62px;color:var(--white)}
.card{top:200px;width:323px;height:234px;background:var(--white);box-shadow:0 2px 6px rgba(0,0,0,.25);text-align:center}
.card-icon{position:absolute;left:121px;top:-42px;width:82px;height:82px;border-radius:50%;background:var(--orange);border:4px solid var(--white);display:flex;align-items:center;justify-content:center}
.card h3{margin-top:62px;font-weight:400;font-size:20px;color:#333}
.card p{margin:14px 28px 0;font-size:11.5px;line-height:1.85;color:var(--muted)}
.card .card-link{display:block;margin:14px auto 0;width:120px;border-top:1px solid #ddd;padding-top:10px;font-size:11.5px;color:var(--orange);text-transform:uppercase}

/* testimonials */
.testimonials{top:1612px;height:400px;background:var(--white)}
.testimonials .section-title{top:75px;color:var(--navy)}
.quote{top:162px;width:290px;border-left:1px solid #ccc;padding-left:14px}
.quote p{font-style:italic;font-size:13px;line-height:1.6;color:#555}
.quote p::before{content:"\201C";font-size:26px;color:#999;line-height:0;vertical-align:-8px;margin-right:2px}
.client{margin-top:18px;font-size:26px;font-weight:400;color:#222;height:40px}
.quote .who{margin-top:8px;font-style:italic;font-size:12.5px;color:var(--orange)}

/* what we do */
.whatwedo{top:2012px;height:353px;background:linear-gradient(100deg,#e8761c,#f08a2c 50%,#e57418)}
.whatwedo .section-title{top:52px;color:var(--white)}
.whatwedo-copy{left:160px;top:120px;width:880px;text-align:center;color:var(--white);font-size:12.5px;line-height:1.95}
.outline-btn{left:515px;top:255px;width:142px;height:40px;border:2px solid var(--white);color:var(--white);text-align:center;line-height:36px;font-size:13px}

/* why */
.why{top:2365px;height:415px;background:var(--white)}
.why-art{left:80px;top:70px;width:440px;height:290px;border-radius:6px;background:linear-gradient(150deg,#c9a77e,#8b8e94 60%,#e8e8e8)}
.why h2{left:548px;top:86px;font-family:"Roboto Condensed",Arial,sans-serif;font-weight:400;font-size:31px;color:var(--navy)}
.why-copy{left:552px;top:148px;width:550px;font-size:12.5px;line-height:1.85;color:#555}
.why-copy p+p{margin-top:14px}
.why-btn{left:550px;top:326px;background:var(--orange);color:var(--white);padding:13px 26px;font-size:13px}

/* logo strip */
.strip{top:2780px;height:150px;background:var(--white)}
.strip-item{top:20px;width:190px;height:74px;border:1px solid #ddd;display:flex;align-items:center;justify-content:center;font-size:28px;color:#6b6b6b;font-weight:400}
.strip-arrow{top:40px;font-size:24px;color:#555}

/* footer */
.footer{top:2930px;height:315px;background:var(--navy-deep);color:var(--white)}
.footer-brand{left:100px;top:42px;display:flex;align-items:center;gap:10px}
.footer-brand .brand-mark{background:var(--white)}
.footer-brand .brand-name{color:var(--white)}
.contact-list{left:100px;top:112px;font-size:13px;line-height:1.55}
.contact-row{display:flex;gap:14px;margin-bottom:18px}
.contact-row svg{flex:none;margin-top:2px}
.map{left:365px;top:30px;width:390px;height:185px;background:linear-gradient(135deg,#e6e6e6,#cfcfcf)}
.news{left:808px;top:52px;width:292px}
.news h4{font-size:15px;font-weight:500;text-transform:uppercase}
.news p{margin-top:16px;font-size:12px;line-height:1.7;color:#dfe6ef}
.news .field{margin-top:16px;height:40px;background:var(--white);color:#888;font-size:12px;padding:13px 14px}
.news .submit{margin-top:16px;background:var(--orange);color:var(--white);padding:12px 18px;font-size:12px;display:inline-block}

.copyright{top:3245px;height:58px;background:var(--orange);color:var(--white);font-size:12px;text-align:center;line-height:58px}
</style>
</head>
<body>

<div class="block topbar">
  <div class="topbar-links">
    <span><svg width="11" height="11" viewBox="0 0 24 24"><path fill="#fff" d="M6.6 10.8a15 15 0 0 0 6.6 6.6l2.2-2.2a1 1 0 0 1 1-.25 11 11 0 0 0 3.6.6 1 1 0 0 1 1 1V20a1 1 0 0 1-1 1A17 17 0 0 1 3 4a1 1 0 0 1 1-1h3.5a1 1 0 0 1 1 1 11 11 0 0 0 .6 3.6 1 1 0 0 1-.25 1z"/></svg>Call Us + 1300 552 804</span>
    <span><svg width="12" height="10" viewBox="0 0 24 18"><path fill="#fff" d="M0 0h24v18H0zm2 2v.5l10 7 10-7V2z"/></svg>info@bravuln.example</span>
    <span><svg width="10" height="11" viewBox="0 0 24 24"><circle cx="12" cy="7" r="5" fill="#fff"/><path fill="#fff" d="M2 24c0-6 4.5-10 10-10s10 4 10 10z"/></svg>Contact Me</span>
  </div>
</div>

<header class="block header">
  <div class="brand"><span class="brand-mark"></span><span class="brand-name">Kavreo</span></div>
  <nav class="nav">
    <span class="active">Home</span><span>About Us</span><span>Portfolio</span><span>Contact Us</span>
    <svg width="12" height="12" viewBox="0 0 24 24"><circle cx="10" cy="10" r="7" fill="none" stroke="#333" stroke-width="3"/><path d="M15 15l7 7" stroke="#333" stroke-width="3"/></svg>
  </nav>
</header>

<section class="block hero" role="img" aria-label="Photo of a smiling merchant checking her online store on a phone">
  <div class="abs hero-text">
    <h1>Ecommerce by Bravuln</h1>
    <h2>Powering your online business.</h2>
  </div>
  <span class="abs btn hero-btn">Sign up now</span>
  <span class="abs hero-arrow" style="left:38px">&#8249;</span>
  <span class="abs hero-arrow" style="right:38px">&#8250;</span>
  <span class="abs badge" style="left:963px;background:var(--orange)" role="img" aria-label="Torvista Ceritified Solution Provider badge"></span>
  <span class="abs badge" style="left:1036px;background:#9a9a9a" role="img" aria-label="Torvista Certified Developer badge"></span>
</section>

<section class="block welcome">
  <div class="abs welcome-title"><div class="l1">WELCOME TO</div><div class="l2">Kavreo eCommerce</div></div>
  <div class="abs welcome-copy">
    <p>Nemo enim ipsam voluptatem quia voluptas sit aspernatur aut odit aut fugit, sed quia consequuntur magni dolores eos qui ratione voluptatem sequi nesciunt. Neque porro quisquam est, qui dolorem ipsum quia dolor sit amet, consectetur, adipisci velit, sed quia non numquam.</p>
    <p>Nemo enim ipsam voluptatem quia voluptas sit aspernatur aut odit aut fugit, sed quia consequuntur magni dolores eos qui ratione voluptatem sequi nesciunt. Neque porro quisquam.</p>
  </div>
  <span class="abs btn welcome-btn">Read more</span>
  <div class="abs welcome-art" role="img" aria-label="Illustration of a shopping bag with a pointer cursor"></div>
</section>

<section class="block services" role="region" aria-label="Kavreo online business">
  <h2 class="abs section-title">KAVREO ONLINE BUSINESS</h2>
  <div class="abs card" style="left:98px">
    <div class="card-icon"><svg width="40" height="40" viewBox="0 0 24 24"><path d="M5 12l5 5 9-10" fill="none" stroke="#fff" stroke-width="2.8"/></svg></div>
    <h3>Why Kavreo?</h3>
    <p>Fast Torvista-based online stores, built on time and to specification, backed by effective, focused support, means that our clients are among</p>
    <span class="card-link">Contact us now!</span>
  </div>
  <div class="abs card" style="left:438px">
    <div class="card-icon"><svg width="36" height="36" viewBox="0 0 24 24"><rect x="4" y="4" width="16" height="16" rx="2" fill="none" stroke="#fff" stroke-width="2.6"/></svg></div>
    <h3>Why Torvista?</h3>
    <p>Fast Torvista-based online stores, built on time and to specification, backed by effective, focused support, means that our clients are among</p>
    <span class="card-link">Contact us now!</span>
  </div>
  <div class="abs card" style="left:779px">
    <div class="card-icon"><svg width="38" height="38" viewBox="0 0 24 24"><circle cx="12" cy="8" r="4.5" fill="#fff"/><path d="M3 22c0-5 4-8.5 9-8.5s9 3.5 9 8.5z" fill="#fff"/></svg></div>
    <h3>What We Do.</h3>
    <p>Fast Torvista-based online stores, built on time and to specification, backed by effective, focused support, means that our clients are among</p>
    <span class="card-link">Contact us now!</span>
  </div>
</section>

<section class="block testimonials">
  <h2 class="abs section-title">TESTIMONIALS</h2>
  <div class="abs quote" style="left:100px">
    <p>Kavreo are great developers whose concentration on detail does not compromise the delivery of work.</p>
    <div class="client">Lace &amp; Loom</div>
    <div class="who">Marcus Hale, Lace &amp; Loom</div>
  </div>
  <div class="abs quote" style="left:455px">
    <p>Kavreo went above and beyond by delivering great work in excellent time frames.</p>
    <div class="client" style="margin-top:40px">Glimmer</div>
    <div class="who">Oliver Brandt, Glimmer</div>
  </div>
  <div class="abs quote" style="left:810px">
    <p>Kavreo are great developers whose concentration on detail does not compromise the delivery of work.</p>
    <div class="client">Tailor Row</div>
    <div class="who">Peter Vandaal, Tailor Row</div>
  </div>
</section>

<section class="block whatwedo">
  <h2 class="abs section-title">WHAT WE DO</h2>
  <p class="abs whatwedo-copy">From support, maintenance and upgrades to redesigns, migrations and full site builds, we make your online store do what you need it to do Sed ut perspiciatis unde omnis iste natus error sit voluptatem accusantium doloremque laudantium, totam rem aperiam, eaque ipsa quae ab illo inventore veritatis et quasi archite cto beatae vitae dicta sunt explicabo enoium doloremque laudantium, totam rem aperiam, eaque ipsa quae ab illo inventore veritatis et quasi archite cto beatae vitae dicta sunt explicabo.emo enim ipsam voluptatem quia. aspernatur aut odit</p>
  <span class="abs btn outline-btn">Read more</span>
</section>

<section class="block why">
  <div class="abs why-art" role="img" aria-label="Illustration of a shopping cart with parcels on a tablet"></div>
  <h2 class="abs">WHY TORVISTA AND KAVREO?</h2>
  <div class="abs why-copy">
    <p>Torvista is the world's leading open source eCommerce platform. No other open-source or free system offers out-of-the-box functionality and search engine friendliness comparable to Torvista CE. aspernatur aut odit aut fugit, sed quia consequunt</p>
    <p>Sed ut perspiciatis unde omnis iste natus error sit voluptatem accusantium doloremque laudantium, totam rem aperiam, eaque ipsa quae ab illo inventore veritatis et quasi archite cto beatae vitae dicta sunt explicabo.emo enim ipsam voluptatem quia.</p>
  </div>
  <span class="abs btn why-btn">Read more about Torvista &amp; Kavreo</span>
</section>

<section class="block strip" aria-label="Technology partners">
  <span class="abs strip-arrow" style="left:74px">&#8249;</span>
  <div class="abs strip-item" style="left:115px">Torvista</div>
  <div class="abs strip-item" style="left:310px">QRX</div>
  <div class="abs strip-item" style="left:505px">DataVane</div>
  <div class="abs strip-item" style="left:700px">NCB</div>
  <div class="abs strip-item" style="left:895px;font-size:20px;letter-spacing:3px">HARROWBY</div>
  <span class="abs strip-arrow" style="left:1103px">&#8250;</span>
</section>

<footer class="block footer">
  <div class="abs footer-brand"><span class="brand-mark"></span><span class="brand-name">Kavreo</span></div>
  <div class="abs contact-list">
    <div class="contact-row"><svg width="14" height="18" viewBox="0 0 24 30"><path fill="#fff" d="M12 0a10 10 0 0 0-10 10c0 8 10 20 10 20s10-12 10-20A10 10 0 0 0 12 0zm0 14a4 4 0 1 1 0-8 4 4 0 0 1 0 8z"/></svg><span>Suite 42, Level 3|8 Wattlebrook<br>Lane|Fernvale Heights<br>VIC 3999</span></div>
    <div class="contact-row"><svg width="16" height="16" viewBox="0 0 24 24"><path fill="#fff" d="M6.6 10.8a15 15 0 0 0 6.6 6.6l2.2-2.2a1 1 0 0 1 1-.25 11 11 0 0 0 3.6.6 1 1 0 0 1 1 1V20a1 1 0 0 1-1 1A17 17 0 0 1 3 4a1 1 0 0 1 1-1h3.5a1 1 0 0 1 1 1 11 11 0 0 0 .6 3.6 1 1 0 0 1-.25 1z"/></svg><span>1300 648 907</span></div>
    <div class="contact-row"><svg width="16" height="12" viewBox="0 0 24 18"><path fill="none" stroke="#fff" stroke-width="2" d="M1 1h22v16H1zM1 1l11 8 11-8"/></svg><span>support@kavreo.example</span></div>
  </div>
  <div class="abs map" role="img" aria-label="Grayscale street map showing the office location"></div>
  <div class="abs news">
    <h4>Torvista Support &amp; Security Updates</h4>
    <p>Excepteur sint occaecat cupidatat non proident, sunt in culpa qui Excepteur sint occaecat cupidatat non</p>
    <div class="field">Enter Name</div>
    <span class="btn submit">Subscribe</span>
  </div>
</footer>

<div class="block copyright">Copyright 2016 | All Rights Reserved – Kavreo</div>

</body>
</html>
```